Personal training and nutrition business needs business card design

We need a business card that outlays our services and invites potential customers to join our team and take the first step to a healthier and more enjoyable life. We cater for any level of fitness and specialize in weight loss and conditioning, strength training, muscle gain and strength endurance. Whether you are just starting off or need some help getting to the next level of your journey we are here to get the job done.
We specialize in one on one or one on two personal training sessions and each program will be custom made to suit individual fitness goals of our clients

```html
<!DOCTYPE html>
<html lang="en">
<head>
<meta charset="utf-8">
<title>Stride &amp; Rise – Business Card</title>
<link rel="stylesheet" href="https://fonts.googleapis.com/css2?family=Exo+2:ital,wght@1,800&family=Roboto:wght@400;500;700&display=swap">
<style>
  :root {
    --page: #2a2a2a;
    --purple-deep: #553a86;
    --purple-mid: #7a4696;
    --purple-light: #9b55a3;
    --band: #5b3b8c;
    --strip: #a25aa3;
    --paper: #f0f0f0;
    --ink: #1a1a1a;
    --text: #333333;
    --white-soft: #ecebf2;
  }
  * { margin: 0; padding: 0; box-sizing: border-box; }
  html, body { width: 1200px; height: 1138px; overflow: hidden; }
  body {
    background: var(--page);
    font-family: "Roboto", Arial, sans-serif;
    position: relative;
  }
  .card {
    position: absolute;
    border-radius: 18px;
    overflow: hidden;
  }
  .card-front {
    left: 274px; top: 186px; width: 622px; height: 376px;
    background: linear-gradient(115deg, var(--purple-deep) 0%, var(--purple-mid) 50%, var(--purple-light) 100%);
    display: flex; flex-direction: column; align-items: center; justify-content: center;
    padding-top: 8px;
  }
  .brand-front {
    font-family: "Roboto", Arial, sans-serif;
    font-weight: 700;
    font-size: 50px;
    letter-spacing: 2px;
    color: var(--white-soft);
    line-height: 1;
  }
  .tagline-front {
    margin-top: 18px;
    font-weight: 500;
    font-size: 16px;
    letter-spacing: 2.4px;
    color: var(--white-soft);
  }
  .card-back {
    left: 276px; top: 608px; width: 618px; height: 374px;
    background: var(--paper);
  }
  .brand-lockup {
    position: absolute; left: 40px; top: 42px;
    display: flex; align-items: center; gap: 22px;
  }
  .brand-square {
    width: 78px; height: 78px; border-radius: 6px;
    background: linear-gradient(135deg, var(--band), var(--strip));
  }
  .brand-back {
    font-weight: 700; font-size: 34px; line-height: 1.05;
    letter-spacing: 1.5px; color: var(--ink);
  }
  .person-name {
    position: absolute; left: 34px; top: 198px;
    font-family: "Exo 2", Arial, sans-serif;
    font-style: italic; font-weight: 800;
    font-size: 26px; letter-spacing: 1.5px;
    color: var(--purple-mid);
  }
  .person-role {
    position: absolute; left: 33px; top: 231px;
    font-size: 16px; color: var(--text);
  }
  .address {
    position: absolute; left: 34px; top: 283px;
    font-size: 16px; line-height: 24px; color: var(--text);
  }
  .contacts {
    position: absolute; left: 340px; top: 201px;
    list-style: none;
  }
  .contacts li {
    display: flex; align-items: center; gap: 16px;
    height: 24px; font-size: 16px; color: var(--text);
  }
  .contacts svg { width: 16px; height: 16px; fill: var(--band); flex: none; }
  .footer-strip {
    position: absolute; left: 0; bottom: 0; width: 100%; height: 14px;
    background: linear-gradient(90deg, var(--strip), var(--band));
  }
  .footer-band {
    position: absolute; right: 0; bottom: 0; width: 364px; height: 46px;
    background: var(--band);
    clip-path: polygon(18px 0, 100% 0, 100% 100%, 0 100%);
    display: flex; align-items: center; justify-content: flex-end;
    padding-right: 19px;
    font-size: 16px; color: var(--white-soft);
  }
</style>
</head>
<body>
  <section class="card card-front">
    <div class="brand-front">STRIDE &amp; RISE</div>
    <div class="tagline-front">PERSONAL TRAINING &nbsp;|&nbsp; NUTRITION &nbsp;|&nbsp; MOTIVATION</div>
  </section>

  <section class="card card-back">
    <div class="brand-lockup">
      <div class="brand-square"></div>
      <div class="brand-back">STRIDE<br>&amp; RISE</div>
    </div>

    <div class="person-name">MARK ROWAN</div>
    <div class="person-role">Personal Trainer</div>
    <div class="address">418 Maple Crest Drive<br>Lakeview Texas 75000</div>

    <ul class="contacts">
      <li>
        <svg viewBox="0 0 16 16" aria-hidden="true"><path d="M3 2h3l1.2 3-1.7 1.2a8 8 0 0 0 4.3 4.3L11 8.8l3 1.2v3a1.5 1.5 0 0 1-1.6 1.5A12 12 0 0 1 1.5 3.6 1.5 1.5 0 0 1 3 2z"/></svg>
        +1 (555) 014-2290
      </li>
      <li>
        <svg viewBox="0 0 16 16" aria-hidden="true"><path d="M1 3h14v10H1z M1.5 3.5 8 9l6.5-5.5" stroke="#f0f0f0" stroke-width="1.2"/></svg>
        mark@strideandrise.com
      </li>
      <li>
        <svg viewBox="0 0 16 16" aria-hidden="true"><circle cx="8" cy="8" r="7"/><path d="M1 8h14M8 1c-2.5 2.5-2.5 11.5 0 14M8 1c2.5 2.5 2.5 11.5 0 14" stroke="#f0f0f0" stroke-width="1" fill="none"/></svg>
        www.strideandrise.com
      </li>
    </ul>

    <div class="footer-strip"></div>
    <div class="footer-band">Personal Training | Nutrition | Motivation</div>
  </section>
</body>
</html>
```